Business Card Design

I already have a company logo for my company. I have a logo for the manufacturer we represent. I want a professional business card design.

```html
<!DOCTYPE html>
<html lang="en">
<head>
<meta charset="utf-8">
<title>Beacon Ridge Partners — Business Card</title>
<link href="https://fonts.googleapis.com/css2?family=Open+Sans:wght@400;600;700&display=swap" rel="stylesheet">
<style>
  :root {
    --backdrop: #232323;
    --card: #ffffff;
    --gold: #b98e2f;
    --red: #e3202a;
    --ink: #1e1e1e;
    --muted: #444444;
  }
  * { margin: 0; padding: 0; box-sizing: border-box; }
  html, body { width: 1200px; height: 780px; overflow: hidden; }
  body {
    background: var(--backdrop);
    font-family: "Open Sans", Arial, sans-serif;
    position: relative;
  }
  .card {
    position: absolute;
    top: 241px;
    width: 520px;
    height: 298px;
    background: var(--card);
    overflow: hidden;
    box-shadow: 0 10px 30px rgba(0,0,0,0.45);
  }
  .card--front { left: 50px; }
  .card--back { left: 630px; }

  .front-band { position: absolute; inset: 0; width: 100%; height: 100%; }

  .holder { position: absolute; left: 38px; top: 36px; }
  .holder__name { font-size: 25px; font-weight: 700; line-height: 1.1; }
  .holder__first { color: var(--gold); }
  .holder__last { color: var(--red); }
  .holder__title { font-size: 12.5px; color: var(--ink); margin-top: 4px; margin-left: 2px; }

  .brand {
    position: absolute;
    display: flex;
    align-items: center;
    gap: 8px;
  }
  .brand__mark { width: 12px; height: 12px; background: var(--red); flex: none; }
  .brand__name { font-weight: 700; color: var(--red); line-height: 1.15; }
  .card--front .brand { left: 292px; top: 40px; }
  .card--front .brand__name { font-size: 17px; }

  .divider {
    position: absolute;
    left: 262px; top: 118px;
    width: 2px; height: 72px;
    background: var(--gold);
  }
  .contacts { position: absolute; left: 282px; top: 116px; list-style: none; }
  .contacts li {
    display: flex; align-items: center; gap: 9px;
    font-size: 13px; color: var(--ink);
    height: 25px;
  }
  .contacts svg { width: 13px; height: 13px; flex: none; }

  .address {
    position: absolute;
    left: 40px; bottom: 22px;
    font-size: 13px; color: #ffffff;
    letter-spacing: 0.2px;
  }

  .card--back .brand {
    left: 50%; top: 50%;
    transform: translate(-50%, -50%);
    gap: 12px;
  }
  .card--back .brand__mark { width: 18px; height: 18px; }
  .card--back .brand__name { font-size: 28px; white-space: nowrap; }
  .back-rule {
    position: absolute;
    left: 130px; right: 130px; top: 182px;
    height: 3px; background: var(--gold);
  }
</style>
</head>
<body>

<section class="card card--front" aria-label="Business card front">
  <svg class="front-band" viewBox="0 0 520 298" preserveAspectRatio="none" aria-hidden="true">
    <path d="M0,196 C140,262 340,262 520,222 L520,298 L0,298 Z" fill="var(--gold)"/>
    <path d="M0,196 C140,262 340,262 520,222" fill="none" stroke="#ffffff" stroke-width="8"/>
    <path d="M14,178 C150,252 350,252 506,212" fill="none" stroke="var(--red)" stroke-width="3"/>
  </svg>

  <div class="holder">
    <h1 class="holder__name"><span class="holder__first">Lena</span> <span class="holder__last">Marchetti</span></h1>
    <p class="holder__title">Managing Director</p>
  </div>

  <div class="brand">
    <span class="brand__mark"></span>
    <span class="brand__name">Beacon Ridge<br>Partners</span>
  </div>

  <div class="divider"></div>

  <ul class="contacts">
    <li>
      <svg viewBox="0 0 24 24" aria-hidden="true"><path fill="var(--gold)" d="M6.6 10.8a15.1 15.1 0 0 0 6.6 6.6l2.2-2.2c.3-.3.7-.4 1-.2 1.1.4 2.3.6 3.6.6.6 0 1 .4 1 1V20c0 .6-.4 1-1 1A17 17 0 0 1 3 4c0-.6.4-1 1-1h3.5c.6 0 1 .4 1 1 0 1.3.2 2.5.6 3.6.1.3 0 .7-.2 1z"/></svg>
      (555) 214-3087
    </li>
    <li>
      <svg viewBox="0 0 24 24" aria-hidden="true"><rect x="2" y="5" width="20" height="14" rx="1.5" fill="var(--gold)"/><path d="M3 6.5l9 6.5 9-6.5" fill="none" stroke="#fff" stroke-width="1.6"/></svg>
      hello@beaconridge.com
    </li>
    <li>
      <svg viewBox="0 0 24 24" aria-hidden="true"><circle cx="12" cy="12" r="10" fill="var(--gold)"/><path d="M2 12h20M12 2c3 3 3 17 0 20M12 2c-3 3-3 17 0 20" fill="none" stroke="#fff" stroke-width="1.3"/></svg>
      www.beaconridge.com
    </li>
  </ul>

  <p class="address">418 Cedar Hollow Rd. Suite 300 Millbrook, TX 75001</p>
</section>

<section class="card card--back" aria-label="Business card back">
  <div class="brand">
    <span class="brand__mark"></span>
    <span class="brand__name">Beacon Ridge Partners</span>
  </div>
  <div class="back-rule"></div>
</section>

</body>
</html>
```